Shine Fox Auto Care Business Card

2 side business card design for an auto detailing business

Target Market(s)

Auto detailing

Contact Information for Business Card

Things included

The business name “Shine Fox Auto Care”
Mark Dunrow
(403)271-6094
Harlow Creek, Sk

Services offered - complete interior& exterior detail
- paint correction & protection
- ceramic coating
- trim restore
- auto carpet & seat cleaning

Requirements
Must have
• Colours that are in my logo

Services offered

My name Mark Dunrow
403-271-6094
Harlow Creek, Sk

Not too sure in what order for these ?
Website. Shinefoxautocare.com
Instagram Shinefoxautocare
Email. Shinefoxautoac@mailvento.com

```html
<!DOCTYPE html>
<html lang="en">
<head>
<meta charset="utf-8">
<title>Shine Fox Auto Care – Business Card</title>
<link href="https://fonts.googleapis.com/css2?family=Michroma&family=Arimo:wght@400;700&display=swap" rel="stylesheet">
<style>
  :root {
    --bg: #2a2a2c;
    --card-light: #ffffff;
    --card-dark: #1d1d1f;
    --pattern-top: #2c2c2f;
    --brand-red: #9a0f12;
    --ink: #111111;
    --rule: #9a9a9a;
    --on-dark: #f2f2f2;
    --rule-dark: #8a8a8a;
  }
  * { box-sizing: border-box; margin: 0; padding: 0; }
  html, body { width: 1200px; height: 1108px; overflow: hidden; }
  body {
    background: var(--bg);
    font-family: "Arimo", Arial, sans-serif;
    display: flex;
    align-items: center;
    justify-content: center;
    gap: 70px;
  }
  .card {
    width: 400px;
    height: 680px;
    border-radius: 26px;
    position: relative;
    overflow: hidden;
    display: flex;
    flex-direction: column;
    align-items: center;
  }

  /* Front */
  .card-front { background: var(--card-light); color: var(--ink); padding-top: 110px; }
  .brand-ring {
    width: 110px; height: 110px;
    border: 14px solid var(--brand-red);
    border-radius: 50%;
  }
  .brand-name {
    font-family: "Michroma", sans-serif;
    font-weight: 400;
    color: var(--ink);
    text-align: center;
    font-size: 34px;
    line-height: 1.15;
    margin-top: 14px;
    letter-spacing: 1px;
  }
  .brand-name .tagline {
    display: block;
    font-size: 20px;
    letter-spacing: 20px;
    margin-right: -20px;
    color: var(--brand-red);
  }
  .person-name {
    font-family: "Michroma", sans-serif;
    font-weight: 400;
    color: var(--brand-red);
    font-size: 27px;
    margin-top: 96px;
  }
  .icon-rule {
    display: flex; align-items: center; gap: 8px;
    width: 300px; margin-top: 12px;
  }
  .icon-rule::before, .icon-rule::after {
    content: ""; flex: 1; height: 1px; background: var(--rule);
  }
  .icon-badge {
    width: 26px; height: 26px; border-radius: 50%;
    border: 1.5px solid var(--brand-red);
    display: flex; align-items: center; justify-content: center;
  }
  .icon-badge svg { width: 16px; height: 16px; fill: var(--brand-red); }
  .contact-list { text-align: center; font-size: 19px; line-height: 1.3; margin-top: 8px; }
  .contact-list .accent { color: var(--brand-red); }
  .location { font-size: 19px; margin-top: 6px; }

  /* Back */
  .card-back { background: var(--card-dark); color: var(--on-dark); }
  .pattern-field {
    position: absolute; inset: 0;
    background: linear-gradient(180deg, var(--pattern-top) 0%, var(--card-dark) 100%);
  }
  .back-brand {
    position: relative; margin-top: 200px;
    display: flex; flex-direction: column; align-items: center; gap: 8px;
  }
  .back-brand .ring { width: 44px; height: 44px; border: 6px solid var(--brand-red); border-radius: 50%; }
  .back-brand .name { font-family: "Michroma", sans-serif; font-size: 13px; color: var(--on-dark); letter-spacing: 1px; }
  .services-heading {
    position: relative; margin-top: 96px;
    display: flex; align-items: center; gap: 10px; width: 340px;
    font-weight: 700; font-size: 20px; letter-spacing: 0.5px;
  }
  .services-heading::before, .services-heading::after {
    content: ""; flex: 1; height: 1px; background: var(--on-dark);
  }
  .services-sub { position: relative; font-size: 13px; margin-top: 4px; letter-spacing: 0.3px; }
  .services-list { position: relative; list-style: none; text-align: center; font-size: 22px; line-height: 1.3; margin-top: 10px; }
  .social-rule { position: relative; display: flex; align-items: center; gap: 10px; width: 330px; margin-top: 18px; }
  .social-rule::before, .social-rule::after { content: ""; flex: 1; height: 1px; background: var(--rule-dark); }
  .social-dot { width: 22px; height: 22px; border-radius: 50%; background: var(--on-dark); }
  .social-handle { position: relative; font-size: 18px; margin-top: 6px; }
</style>
</head>
<body>
  <section class="card card-front">
    <div class="brand-ring"></div>
    <h1 class="brand-name">SHINE FOX<span class="tagline">AUTO CARE</span></h1>
    <h2 class="person-name">MARK DUNROW</h2>
    <div class="icon-rule">
      <span class="icon-badge"><svg viewBox="0 0 24 24"><path d="M6.6 10.8a15 15 0 006.6 6.6l2.2-2.2c.3-.3.7-.4 1-.2 1.1.4 2.3.6 3.6.6.6 0 1 .4 1 1V20c0 .6-.4 1-1 1A17 17 0 013 4c0-.6.4-1 1-1h3.5c.6 0 1 .4 1 1 0 1.3.2 2.5.6 3.6.1.3 0 .7-.2 1z"/></svg></span>
      <span class="icon-badge"><svg viewBox="0 0 24 24"><path d="M3 5h18v14H3zm2 2v.5l7 5 7-5V7l-7 5z"/></svg></span>
      <span class="icon-badge"><svg viewBox="0 0 24 24"><path d="M12 2a10 10 0 100 20 10 10 0 000-20zm0 2c1 1.3 1.8 3 2.1 5H9.9C10.2 7 11 5.3 12 4zm-7.7 7h3.6a14 14 0 000 2H4.3a8 8 0 010-2zm5.6 2a12 12 0 010-2h4.2a12 12 0 010 2zm6.2 0a14 14 0 000-2h3.6a8 8 0 010 2zM12 20c-1-1.3-1.8-3-2.1-5h4.2c-.3 2-1.1 3.7-2.1 5z"/></svg></span>
    </div>
    <div class="contact-list">
      <p>(403)271-6094</p>
      <p>Shinefoxautocare@mailvento.com</p>
      <p>www.<span class="accent">Shinefoxautocare</span>.com</p>
    </div>
    <div class="icon-rule">
      <span class="icon-badge"><svg viewBox="0 0 24 24"><path d="M12 2a7 7 0 00-7 7c0 5 7 13 7 13s7-8 7-13a7 7 0 00-7-7zm0 9.5A2.5 2.5 0 1112 6.5a2.5 2.5 0 010 5z"/></svg></span>
    </div>
    <p class="location">Harlow Creek, Sk</p>
  </section>

  <section class="card card-back">
    <div class="pattern-field" role="img" aria-label="Tonal repeating brand pattern background"></div>
    <div class="back-brand">
      <span class="ring"></span>
      <span class="name">SHINE FOX</span>
    </div>
    <h3 class="services-heading">SERVICES OFFERED</h3>
    <p class="services-sub">COMPLETE INTERIOR &amp; EXTERIOR DETAIL</p>
    <ul class="services-list">
      <li>Paint correction &amp; protection</li>
      <li>Ceramic coating</li>
      <li>Trim restore</li>
      <li>Auto carpet &amp; seat cleaning</li>
    </ul>
    <div class="social-rule"><span class="social-dot"></span></div>
    <p class="social-handle">Shinefoxautocare</p>
  </section>
</body>
</html>
```